Business card design for holistic health care clinic

We need a double-sided business card design for our holistic health care clinic that integrates our logo design and also its color scheme. My business is called Valmira. It is an integrative medicine clinic. You have already done the logo for me. Please ensure an elegant and upscale design that is not cluttered, but still has all the necessary information (please see below for details).

Target Market(s)

Wellness, fitness, rehabilitation for educated, well-traveled open-minded clients who are focused on natural, organic, balanced and preventive healthcare and lifestyle.

Industry/Entity Type

Medical

Contact Information for Business Card

Modern, clean.

Number of Pages Required

1 page

Font styles to use
Serif
Sans Serif

Colors

Designer to choose colors to be used in the design.

Requirements
Must have
• Logo on one side, all other information on the other side.
• Other information should include:
• Tobias Wrenfeld - DOE, CPT, LMT
• 4100 East Marrow Drive
• Austin, TX 78119
• 512 555 0148
• 818 555 0192
• info@ValmiraHealth.example
• t.wrenfeld@ValmiraHealth.example
Nice to have
• Darker background on front - but not totally black - shaded/dark gray.

```html
<!DOCTYPE html>
<html lang="en">
<head>
<meta charset="utf-8">
<title>Valmira – Business Card</title>
<link href="https://fonts.googleapis.com/css2?family=Nunito:wght@800&family=Source+Sans+3:wght@400&display=swap" rel="stylesheet">
<style>
  :root {
    --stage: #000000;
    --card-front: #ffffff;
    --card-back: #13739c;
    --brand-blue: #1b8fcf;
    --ink: #333333;
    --on-dark: #ffffff;
  }
  * { margin: 0; padding: 0; box-sizing: border-box; }
  html, body {
    width: 1200px; height: 900px; overflow: hidden;
    background: var(--stage);
    font-family: "Source Sans 3", "Myriad Pro", sans-serif;
  }
  .stage { position: relative; width: 1200px; height: 900px; }
  .card {
    position: absolute; top: 300px;
    width: 442px; height: 273px; border-radius: 12px;
  }
  .card--info { left: 152px; background: var(--card-front); }
  .card--brand { left: 622px; background: var(--card-back); }

  .brand-name {
    position: absolute;
    font-family: "Nunito", sans-serif; font-weight: 800;
    font-size: 44px; letter-spacing: 0.5px; line-height: 1;
    white-space: nowrap;
  }
  .card--info .brand-name { right: 28px; top: 48px; color: var(--brand-blue); }
  .card--brand .brand-name { right: 34px; top: 56px; color: var(--on-dark); }

  .person { position: absolute; left: 27px; top: 50px; }
  .person__name {
    font-size: 18.5px; color: var(--brand-blue);
    letter-spacing: 0.4px; line-height: 1.1;
  }
  .person__credentials { font-size: 12.5px; color: var(--ink); margin-top: 4px; }

  .contact-list {
    position: absolute; left: 26px; top: 185px; list-style: none;
    font-size: 12.5px; color: var(--ink);
  }
  .contact-list li { display: flex; align-items: center; height: 16px; }
  .contact-list svg { width: 10px; height: 10px; margin-right: 4px; fill: var(--brand-blue); }

  .address {
    position: absolute; right: 27px; top: 215px; text-align: right;
    font-size: 12.5px; color: var(--ink); line-height: 16px; font-style: normal;
  }
  .website {
    position: absolute; right: 33px; top: 228px;
    font-size: 12.5px; color: var(--on-dark);
  }
</style>
</head>
<body>
<main class="stage">
  <section class="card card--info" aria-label="Business card, contact side">
    <div class="brand-name">VALMIRA</div>
    <div class="person">
      <h1 class="person__name">TOBIAS WRENFELD</h1>
      <p class="person__credentials">DOE,CPT,LMT</p>
    </div>
    <ul class="contact-list">
      <li><svg viewBox="0 0 10 10" aria-hidden="true"><path d="M3 0h4a1 1 0 0 1 1 1v8a1 1 0 0 1-1 1H3a1 1 0 0 1-1-1V1a1 1 0 0 1 1-1zm0 1.5v6h4v-6z"/></svg>512 555 0148</li>
      <li><svg viewBox="0 0 10 10" aria-hidden="true"><path d="M0 4c0-2 2-3 5-3s5 1 5 3v1H7.5V3.8h-5V5H0zM2 6h6l1 3H1z"/></svg>818 555 0192</li>
      <li><svg viewBox="0 0 10 10" aria-hidden="true"><path d="M0 2h10v.8L5 6 0 2.8zm0 2l5 3.2L10 4v4H0z"/></svg>info@ValmiraHealth.example</li>
      <li><svg viewBox="0 0 10 10" aria-hidden="true"><path d="M0 2h10v.8L5 6 0 2.8zm0 2l5 3.2L10 4v4H0z"/></svg>t.wrenfeld@ValmiraHealth.example</li>
    </ul>
    <address class="address">4100 East Marrow Drive<br>Austin, TX 78119</address>
  </section>

  <section class="card card--brand" aria-label="Business card, brand side">
    <div class="brand-name">VALMIRA</div>
    <p class="website">www.ValmiraHealth.example</p>
  </section>
</main>
</body>
</html>
```